Inspirational Quotes Poster Set

Brookloft is a stylish coworking space, which has a design-oriented vintage look from the 60's with an industrial touch (www.brookloft-example.com) Brookloft Quote Poster Set of 16 posters. The poster should be typo oriented and rather simple. Reflecting a bit the clean billboard design from the sixties. Minimal / simple graphical elements

Target Market(s)

Startups and Entrepreneurs

Industry/Entity Type

Startup

Font styles to use
Sans Serif

Colors

Designer to choose colors to be used in the design.

Requirements
Must have
• Posters need to be on and very stylish

```html
<!DOCTYPE html>
<html lang="en">
<head>
<meta charset="utf-8">
<title>Brookloft Quote Poster Set — Execution</title>
<link rel="stylesheet" href="https://fonts.googleapis.com/css2?family=Archivo:wdth,wght@62..125,100..900&display=swap">
<style>
  :root {
    --poster-blue: #1170b6;
    --glow-light: #a3b5df;
    --glow-mid: #7d9dd2;
    --paper-white: #ffffff;
    --quote-font: "Archivo", "Helvetica Neue", Arial, sans-serif;
  }
  html, body {
    margin: 0;
    padding: 0;
    width: 801px;
    height: 1200px;
    overflow: hidden;
    background: var(--poster-blue);
  }
  .poster {
    position: relative;
    width: 801px;
    height: 1200px;
    background: var(--poster-blue);
    overflow: hidden;
    font-family: var(--quote-font);
  }
  .lamp-illustration {
    position: absolute;
    left: 0;
    top: 0;
    width: 801px;
    height: 1000px;
    background: linear-gradient(180deg,
      var(--poster-blue) 0%,
      var(--glow-light) 22%,
      var(--glow-mid) 55%,
      var(--poster-blue) 100%);
  }
  .quote {
    position: absolute;
    inset: 0;
    display: block;
  }
  .quote-line {
    fill: var(--paper-white);
    font-family: var(--quote-font);
    font-size: 124px;
    font-weight: 800;
    font-stretch: 125%;
    font-variation-settings: "wdth" 125;
  }
  .attribution {
    position: absolute;
    left: 70px;
    top: 1016px;
    margin: 0;
    color: var(--paper-white);
    font-size: 24px;
    line-height: 28px;
    font-weight: 700;
    font-stretch: 125%;
    font-variation-settings: "wdth" 125;
  }
  .brand-name {
    position: absolute;
    left: 70px;
    top: 1098px;
    margin: 0;
    color: var(--paper-white);
    font-size: 44px;
    line-height: 50px;
    font-weight: 800;
    letter-spacing: -1.5px;
  }
</style>
</head>
<body>
<main class="poster">
  <div class="lamp-illustration" role="img" aria-label="Illustration area: a pendant light bulb hanging from a cord, casting a wide cone of soft light down over the quote"></div>

  <svg class="quote" width="801" height="1200" viewBox="0 0 801 1200" role="img" aria-label="ideas are commodity. execution of them is not.">
    <text class="quote-line" x="78" y="432" textLength="316" lengthAdjust="spacingAndGlyphs">ideas</text>
    <text class="quote-line" x="76" y="534" textLength="200" lengthAdjust="spacingAndGlyphs">are</text>
    <text class="quote-line" x="76" y="636" textLength="708" lengthAdjust="spacingAndGlyphs">commodity.</text>
    <text class="quote-line" x="76" y="737" textLength="587" lengthAdjust="spacingAndGlyphs">execution</text>
    <text class="quote-line" x="76" y="840" textLength="468" lengthAdjust="spacingAndGlyphs">of them</text>
    <text class="quote-line" x="78" y="942" textLength="353" lengthAdjust="spacingAndGlyphs">is not.</text>
  </svg>

  <p class="attribution">Martin Hale,<br>Halecore Chairman and CEO</p>
  <p class="brand-name">Brookloft</p>
</main>
</body>
</html>
```